Building company buisness cards

We are looking for a sharp modern new look for our business cards.
We are a New Zealand based company that specialises in house and land packages.
We have attached a photo of the current logo and would like to see if it can be improved somehow if needed.
We are open to any colours but we have chosen green at this stage.
Feel free to change the font and make the logo smarter looking.
Play with the colours and see what looks best.

We want a card that looks so good know one will want to throw it away!

Target Market(s)

Home buyers

Industry/Entity Type

Building

Contact Information for Business Card

Derek Tolvane
0217394062
dtolvane@quillmarkhomesteads.co.nz
quillmarkhomesteads.co.nz

Font styles to use
Serif
Sans Serif

Colors

Designer to choose colors to be used in the design.

Requirements
Must have
• Logo and company name on one side, details on the other side
Nice to have
• Color codes for the original green are HEX #4a8028, RGB(74,128,40), CMYK(42,0,69,50)
• Round corners, Raised and/or spot UV

```html
<!DOCTYPE html>
<html lang="en">
<head>
<meta charset="utf-8">
<title>Quillmark Homesteads – Business Card</title>
<link rel="stylesheet" href="https://fonts.googleapis.com/css2?family=Nunito:wght@900&family=Arimo:wght@600&family=Lato:wght@400&display=swap">
<style>
  :root {
    --stage: #231f20;
    --brand-green: #4a8028;
    --paper: #ffffff;
    --ink: #231f20;
    --shadow: #000000;
  }
  * { margin: 0; padding: 0; box-sizing: border-box; }
  html, body { width: 1200px; height: 883px; overflow: hidden; background: var(--stage); }
  .canvas { position: relative; width: 1200px; height: 883px; }

  .card { position: absolute; top: 123px; width: 373px; height: 653px; overflow: hidden; }
  .card--front { left: 170px; background: var(--paper); }
  .card--back { left: 624px; background: var(--brand-green); }

  .brand-dot {
    position: absolute; top: 72px; left: 166px; width: 40px; height: 40px;
    border-radius: 50%; background: var(--brand-green);
  }
  .wordmark {
    position: absolute; top: 128px; left: 0; width: 100%;
    text-align: center;
    font-family: "Nunito", sans-serif; font-weight: 900;
    color: var(--brand-green); letter-spacing: -0.3px;
  }
  .wordmark__line { display: block; }
  .wordmark__line--top { font-size: 25px; line-height: 28px; }
  .wordmark__line--main { font-size: 32px; line-height: 36px; }
  .wordmark-rule {
    position: absolute; top: 203px; left: 121px; width: 112px; height: 1.5px;
    background: var(--brand-green);
  }

  .name-band { position: absolute; left: 0; top: 292px; width: 240px; height: 88px; }
  .name-band svg { display: block; }
  .name-band__text {
    position: absolute; left: 31px; top: 14px;
    font-family: "Arimo", sans-serif; font-weight: 600; color: var(--paper);
  }
  .name-band__name { font-size: 25px; line-height: 30px; }
  .name-band__title { font-size: 22px; line-height: 26px; }

  .contact-list { position: absolute; left: 0; top: 481px; list-style: none; }
  .contact-item { height: 44px; display: flex; align-items: center; }
  .contact-item__bar { width: 27px; height: 7px; background: var(--brand-green); }
  .contact-item__icon { width: 30px; height: 30px; }
  .contact-item__text {
    margin-left: 8px;
    font-family: "Lato", sans-serif; font-size: 17px; color: var(--ink);
    white-space: nowrap;
  }

  .back-wordmark {
    position: absolute; top: 268px; left: 0; width: 100%; text-align: center;
    font-family: "Nunito", sans-serif; font-weight: 900; color: var(--paper);
  }
  .back-wordmark .wordmark__line--top { font-size: 38px; line-height: 44px; }
  .back-wordmark .wordmark__line--main { font-size: 48px; line-height: 56px; }
  .back-url {
    position: absolute; top: 484px; left: 0; width: 100%; text-align: center;
    font-family: "Lato", sans-serif; font-size: 16px; letter-spacing: 1px;
    color: var(--paper);
  }
</style>
</head>
<body>
<main class="canvas">

  <section class="card card--front" aria-label="Business card front">
    <div class="brand-dot" aria-hidden="true"></div>
    <div class="wordmark">
      <span class="wordmark__line wordmark__line--top">quillmark</span>
      <span class="wordmark__line wordmark__line--main">homesteads.</span>
    </div>
    <div class="wordmark-rule"></div>

    <div class="name-band">
      <svg width="240" height="88" viewBox="0 0 240 88" aria-hidden="true">
        <polygon points="0,5 207,5 238,88 0,88" fill="var(--shadow)"/>
        <polygon points="0,0 202,0 232,82 0,82" fill="var(--brand-green)"/>
      </svg>
      <div class="name-band__text">
        <div class="name-band__name">Derek Tolvane</div>
        <div class="name-band__title">Title</div>
      </div>
    </div>

    <ul class="contact-list">
      <li class="contact-item">
        <span class="contact-item__bar"></span>
        <svg class="contact-item__icon" viewBox="0 0 30 30" aria-hidden="true">
          <circle cx="15" cy="15" r="14" fill="var(--paper)" stroke="var(--brand-green)" stroke-width="1.3"/>
          <path d="M10.5 8.5c1-.8 1.8-.4 2.3.5l1 2c.3.7 0 1.2-.5 1.6l-.8.6c.6 1.6 1.8 3 3.4 3.8l.7-.8c.5-.5 1-.7 1.7-.4l2 1c.8.4 1.1 1.2.4 2.1-1.3 1.6-3 1.8-5.1.6-3-1.6-5-4-5.9-7.1-.5-1.6 0-3 .8-3.9z" fill="var(--brand-green)"/>
          <path d="M16.5 9.5a4 4 0 0 1 3.5 3.5M16.5 7a6.5 6.5 0 0 1 6 6" fill="none" stroke="var(--brand-green)" stroke-width="1" stroke-linecap="round"/>
        </svg>
        <span class="contact-item__text">0217394062</span>
      </li>
      <li class="contact-item">
        <span class="contact-item__bar"></span>
        <svg class="contact-item__icon" viewBox="0 0 30 30" aria-hidden="true">
          <circle cx="15" cy="15" r="14" fill="var(--paper)" stroke="var(--brand-green)" stroke-width="1.3"/>
          <rect x="8.5" y="10.5" width="13" height="9" fill="var(--brand-green)"/>
          <path d="M8.5 10.5l6.5 5 6.5-5M8.5 19.5l4.5-4M21.5 19.5l-4.5-4" fill="none" stroke="var(--paper)" stroke-width="0.9"/>
        </svg>
        <span class="contact-item__text">dtolvane@quillmarkhomesteads.co.nz</span>
      </li>
      <li class="contact-item">
        <span class="contact-item__bar"></span>
        <svg class="contact-item__icon" viewBox="0 0 30 30" aria-hidden="true">
          <circle cx="15" cy="15" r="14" fill="var(--paper)" stroke="var(--brand-green)" stroke-width="1.3"/>
          <g fill="none" stroke="var(--brand-green)" stroke-width="0.9">
            <circle cx="15" cy="15" r="7.5"/>
            <ellipse cx="15" cy="15" rx="3.3" ry="7.5"/>
            <path d="M7.5 15h15M8.5 11.3h13M8.5 18.7h13M15 7.5v15"/>
          </g>
        </svg>
        <span class="contact-item__text">quillmarkhomesteads.co.nz</span>
      </li>
    </ul>
  </section>

  <section class="card card--back" aria-label="Business card back">
    <div class="back-wordmark">
      <span class="wordmark__line wordmark__line--top">quillmark</span>
      <span class="wordmark__line wordmark__line--main">homesteads.</span>
    </div>
    <div class="back-url">www.quillmarkhomesteads.co.nz</div>
  </section>

</main>
</body>
</html>
```